Young, dynamic furniture company needs a new business card design

We require a new business card design for our modern furniture company which supplies furniture and appliances to the property and development market.
Oakridge Interiors has become one of the leading furniture & appliance suppliers to the property market withing London. With over 10 years experience, we have increased our business to supply not only private landlords and managing agents, but also property developers, housing associations and local councils.
We offer not only a complete range of furniture which includes beds, wardrobes, dining sets and sofas, but also a high quality, full delivery and assembly service to help you with all our furnishing needs.

Target Market(s)

Private landlords, estate agents, letting agents, property management companies

Industry/Entity Type

Business

Contact Information for Business Card

Name,
Title,
Address,
Mobile,
Telephone,
Fax, Website, email address

Font styles to use
Sans Serif

Colors
3176b5
0555a3
85abd2
cfdeed

Requirements
Must have
• All the above information for each of our staff, along with our logo

```html
<!DOCTYPE html>
<html lang="en">
<head>
<meta charset="utf-8">
<title>Oakridge Interiors — Business Card</title>
<link href="https://fonts.googleapis.com/css2?family=Roboto+Condensed:wght@300;400&family=Nunito+Sans:wght@400;600&family=Montserrat:wght@700&display=swap" rel="stylesheet">
<style>
  :root {
    --stage: #2a2a2c;
    --card-navy: #283372;
    --card-white: #ffffff;
    --ink-navy: #26357a;
    --ink-dark: #1f1f22;
    --brand-blue: #3176b5;
    --brand-deep: #0555a3;
    --on-navy: #ffffff;
  }
  * { margin: 0; padding: 0; box-sizing: border-box; }
  html, body { width: 1189px; height: 1200px; overflow: hidden; background: var(--stage); }
  .canvas { position: relative; width: 1189px; height: 1200px; }

  .card {
    position: absolute;
    left: 172px;
    width: 855px;
    height: 487px;
    border-radius: 18px;
    overflow: hidden;
  }
  .card--front { top: 68px; background: var(--card-navy); }
  .card--back { top: 627px; background: var(--card-white); }

  .brand { position: absolute; text-align: center; transform: translateX(-50%); }
  .brand__mark { display: block; margin: 0 auto; width: 104px; height: 104px; background: var(--brand-blue); }
  .brand__name {
    font-family: "Roboto Condensed", sans-serif;
    font-weight: 400;
    font-size: 35px;
    line-height: 1;
    white-space: nowrap;
    text-transform: uppercase;
  }
  .brand__tagline {
    font-family: "Roboto Condensed", sans-serif;
    font-weight: 300;
    font-size: 19px;
    line-height: 1;
    white-space: nowrap;
    margin-top: 9px;
    text-transform: uppercase;
  }
  .card--front .brand { left: 427px; top: 155px; color: var(--on-navy); }
  .card--front .brand__mark { margin-bottom: 52px; }
  .card--back .brand { left: 224px; top: 158px; color: var(--ink-dark); }
  .card--back .brand__mark { margin-bottom: 34px; }
  .card--back .brand__name { font-size: 31px; }
  .card--back .brand__tagline { font-size: 17px; margin-top: 7px; }

  .divider { position: absolute; left: 418px; top: 91px; width: 2px; height: 304px; background: var(--ink-navy); }

  .contact { position: absolute; left: 464px; top: 88px; font-family: "Nunito Sans", sans-serif; color: var(--ink-dark); }
  .contact__name { font-family: "Montserrat", sans-serif; font-weight: 700; font-size: 30px; line-height: 1; color: var(--ink-navy); }
  .contact__title { font-size: 22px; line-height: 1; margin-top: 1px; }
  .contact__address { font-size: 23px; line-height: 31px; margin-top: 31px; }
  .contact__list { list-style: none; margin-top: 10px; }
  .contact__item { display: flex; align-items: center; gap: 6px; font-size: 23px; line-height: 29px; }
  .contact__icon { width: 27px; height: 26px; flex: none; }
  .contact__web { font-size: 23px; color: var(--ink-navy); margin-top: 19px; }
</style>
</head>
<body>
<div class="canvas">

  <section class="card card--front" aria-label="Card front">
    <div class="brand">
      <span class="brand__mark"></span>
      <p class="brand__name">Oakridge Interiors</p>
      <p class="brand__tagline">Trade Furniture Solutions</p>
    </div>
  </section>

  <section class="card card--back" aria-label="Card back">
    <div class="brand">
      <span class="brand__mark"></span>
      <p class="brand__name">Oakridge Interiors</p>
      <p class="brand__tagline">Trade Furniture Solutions</p>
    </div>

    <div class="divider"></div>

    <div class="contact">
      <p class="contact__name">DANIEL HART</p>
      <p class="contact__title">Maneger</p>
      <p class="contact__address">Your Address,2nd Ste<br>Fairview, Texas 1234, USA</p>
      <ul class="contact__list">
        <li class="contact__item">
          <svg class="contact__icon" viewBox="0 0 27 26" aria-hidden="true"><rect width="27" height="26" rx="3" fill="var(--ink-navy)"/><path d="M9 5c-2 1-3 3-2 6 1 4 4 8 8 10 2 1 4 0 5-2l-3-3-2 1c-2-1-4-4-4-6l2-1-2-5z" fill="#fff"/></svg>
          123 456 7890
        </li>
        <li class="contact__item">
          <svg class="contact__icon" viewBox="0 0 27 26" aria-hidden="true"><rect width="27" height="26" rx="3" fill="var(--ink-navy)"/><rect x="8" y="5" width="11" height="5" fill="#fff"/><rect x="5" y="10" width="17" height="8" rx="1" fill="#fff"/><rect x="8" y="15" width="11" height="6" fill="#fff" stroke="var(--ink-navy)"/></svg>
          123 456 7890
        </li>
        <li class="contact__item">
          <svg class="contact__icon" viewBox="0 0 27 26" aria-hidden="true"><rect width="27" height="26" rx="3" fill="var(--ink-navy)"/><rect x="9" y="4" width="9" height="18" rx="1.5" fill="#fff"/><rect x="10.5" y="6" width="6" height="6" fill="var(--ink-navy)"/></svg>
          123 456 7890
        </li>
        <li class="contact__item">
          <svg class="contact__icon" viewBox="0 0 27 26" aria-hidden="true"><rect width="27" height="26" rx="3" fill="var(--ink-navy)"/><rect x="5" y="7" width="17" height="12" fill="#fff"/><path d="M5 7l8.5 7L22 7M5 19l6-6M22 19l-6-6" fill="none" stroke="var(--ink-navy)" stroke-width="1.3"/></svg>
          your@yourcompany.com
        </li>
      </ul>
      <p class="contact__web">www.yourcompany.com</p>
    </div>
  </section>

</div>
</body>
</html>
```